Design a calming beauty medical salon & spa website based in Hong Kong

We need help building an informational website for a beauty salon in Hong Kong. The local salon provides facials, massages, body and other slimming treatments in a relaxing environment. We offer some non-invasive medical treatments, such as botox. Having built the business on word of mouth, it is now time for us to launch a website to help market the business better. Website requirements:

-Must be responsive
-Use vibrant but clean colours. not too many, 1-2 colours
-Must be bilingual (switch between Chinese traditional and English)
-Our current website is host on a server, not using any particular platforms like wordpress

Pages:
1/ Homepage
2/ About us (incorporate gallery of salon photos and history of company)
3/ Promotions and latest deals (and leads them to sign up for more info, maybe pop-up small window when you click on a promotion)
4/ Treatment menus
4.1/Body treatments
4.2/ Face treatments
4.3/ Slimming treatments
5/ Showcasing products sold (no e-commerce functionality, just showing off products)
6/ Contact us (tel, address, map, opening hrs)

Footer - must haves include contact us info, privacy policy, terms & conditions, copyright blurb, join our company/employment page (with a form)

For information (comparable websites we like):
http://veltora.com/
http://pambrix.com.hk/tc/aboutpambrix/background.php#centerenvi
Attaching a very first draft concept for this website
Attaching pictures of the beauty salon
Attaching logo

Target Market(s)

Hong Kong based, Chinese, females, 30-50+ age. 90% female clients.

Industry/Entity Type

Beauty Salon

Number of Pages Required

5+ page

Font styles to use
Sans Serif

Colors
f9d9e8
fbd3d4
fee3d5
fbe7d2
fee18a
fbf289
ffffff

Requirements
Must have
• interactive elements on website, such as scrolling banner photo headers
• incorporate photos of website salon
• connect to facebook page

```html
<!DOCTYPE html>
<html lang="en">
<head>
<meta charset="utf-8">
<title>Lumina Beauty – About Us</title>
<link href="https://fonts.googleapis.com/css2?family=Fira+Sans:wght@400;500&family=Fira+Sans+Condensed:wght@600;700&display=swap" rel="stylesheet">
<style>
:root{
  --pink:#f1d4d2;
  --pink-deep:#d9b5b0;
  --button:#c8a09b;
  --lilac-bg:#fbf4fb;
  --purple:#6c1f7c;
  --ink:#2a2a2a;
  --text:#3d3d3d;
  --rule:#d8b3ae;
  --white:#ffffff;
  --black:#111111;
}
*{margin:0;padding:0;box-sizing:border-box}
html,body{width:883px;height:1200px;overflow:hidden;background:var(--white)}
body{position:relative;font-family:"Fira Sans",sans-serif;color:var(--text)}
.abs{position:absolute}

/* header */
.brand{left:64px;top:28px;display:flex;align-items:center;gap:8px}
.brand-dot{width:30px;height:30px;border-radius:50%;background:var(--purple)}
.brand-name{font-family:"Fira Sans",sans-serif;font-weight:500;font-size:22px;color:var(--purple);letter-spacing:.3px}

.utility{left:324px;top:0;width:559px;height:27px;background:var(--pink);border-bottom-left-radius:14px;box-shadow:0 2px 3px rgba(0,0,0,.25);font-size:10px;letter-spacing:1px;color:var(--ink)}
.utility span{position:absolute;top:8px;display:flex;align-items:center;gap:6px;white-space:nowrap}
.utility .sep{top:7px;width:1px;height:12px;background:#e6b9b4}
.ico-sq{display:inline-block;width:10px;height:10px;background:var(--ink);border-radius:2px}

.info{top:45px;font-size:12.5px;letter-spacing:1px;line-height:16px;color:var(--ink);white-space:nowrap}

/* nav */
.nav{left:0;top:92px;width:883px;height:26px;background:var(--pink)}
.nav a{position:absolute;top:0;height:26px;line-height:26px;font-size:12px;letter-spacing:1.2px;color:var(--ink);text-decoration:none;transform:translateX(-50%);white-space:nowrap}
.nav .active-bg{position:absolute;left:158px;top:0;width:103px;height:26px;background:var(--pink-deep)}

/* section titles */
.title{left:0;width:883px;text-align:center;font-family:"Fira Sans Condensed",sans-serif;font-weight:700;font-size:26px;letter-spacing:1.8px;color:var(--black)}
.divider{left:404px;width:75px;height:14px}

.about-copy{left:62px;width:759px;text-align:center;font-size:9.4px;line-height:15.6px;letter-spacing:.25px;color:var(--text)}

/* gallery */
.gallery-band{left:0;top:358px;width:883px;height:560px;background:var(--lilac-bg)}
.photo{width:239px;height:166px}
.p1{left:64px;top:470px;background:linear-gradient(135deg,#b5936e,#d9c2a4 45%,#3e3a3c 75%,#c9a27a)}
.p2{left:322px;top:470px;background:linear-gradient(160deg,#2c2a2a,#3d3a38 60%,#1f1e1e)}
.p3{left:581px;top:470px;background:linear-gradient(140deg,#e6d8c0,#4a3c30 40%,#7a5a3c 70%,#c79a66)}
.p4{left:64px;top:655px;background:linear-gradient(120deg,#6a5848,#d6b49a 40%,#c8aa90 70%,#8a7462)}
.p5{left:322px;top:655px;background:linear-gradient(100deg,#e9e7e5,#f4f2ef 45%,#6a5c48 75%,#2e2a24)}
.p6{left:581px;top:655px;background:linear-gradient(180deg,#b06a2e,#d08a45 50%,#a8602a)}
.zoom{left:431px;top:543px}

.load-more{left:381px;top:840px;width:121px;height:32px;background:var(--button);border-radius:10px 0 10px 0;color:var(--white);font-family:"Fira Sans Condensed",sans-serif;font-weight:600;font-size:11.5px;letter-spacing:1.3px;text-align:center;line-height:32px}

/* footer */
.footer{left:0;top:918px;width:883px;height:261px;background:var(--pink)}
.foot-head{font-family:"Fira Sans Condensed",sans-serif;font-weight:700;font-size:20px;letter-spacing:1.6px;color:var(--black)}
.contact-list{left:64px;top:992px;list-style:none;font-size:10.3px;line-height:16.8px;color:var(--ink);letter-spacing:.3px}
.contact-list li{display:flex;gap:8px;margin-bottom:7px}
.contact-list .ic{flex:0 0 18px;width:18px;height:18px;border-radius:50%;background:var(--black);display:flex;align-items:center;justify-content:center}
.foot-brand{left:342px;top:984px;display:flex;align-items:center;gap:8px}
.foot-about{left:342px;top:1041px;width:205px;font-size:10px;line-height:15.6px;color:var(--ink);letter-spacing:.3px}
.links{left:645px;top:990px;list-style:none;font-size:10px;line-height:16.8px;letter-spacing:.5px;color:var(--ink)}

.copyright{left:0;top:1179px;width:883px;height:21px;background:var(--black);color:var(--white);font-size:10px;letter-spacing:.5px;text-align:center;line-height:21px}
</style>
</head>
<body>

<header>
  <div class="abs brand">
    <span class="brand-dot"></span>
    <span class="brand-name">Lumina Beauty</span>
  </div>

  <div class="abs utility">
    <span style="left:46px">
      <svg width="12" height="9" viewBox="0 0 12 9"><rect width="12" height="9" rx="1" fill="#2a2a2a"/><path d="M0.5 0.8 6 5 11.5 0.8" stroke="#f1d4d2" fill="none" stroke-width="1.2"/></svg>
      Email Us
    </span>
    <i class="abs sep" style="left:161px"></i>
    <span style="left:214px"><i class="ico-sq"></i>Follow Our Community</span>
    <i class="abs sep" style="left:390px"></i>
    <span style="left:441px">ENG &nbsp;|&nbsp; CN</span>
  </div>

  <svg class="abs" style="left:345px;top:47px" width="26" height="26" viewBox="0 0 26 26" aria-hidden="true">
    <path d="M6 3c2-1 3 0 4 2l1 3c.4 1-.3 2-1 2.6l-1 .8c1 2.5 3 4.6 5.5 5.6l.9-1c.7-.7 1.6-1.2 2.6-.8l3 1.2c1.8.8 2.4 2 1.6 3.7-1.3 2.7-4 3.2-7 1.7C10 20 6 15.5 4.4 11 3.3 7.7 3.8 4.3 6 3z" fill="#c99490"/>
  </svg>
  <div class="abs info" style="left:383px">TEL: 23185476<br>WHATSAPP: 6952 1037</div>

  <svg class="abs" style="left:548px;top:46px" width="26" height="26" viewBox="0 0 26 26" aria-hidden="true">
    <rect x="1.5" y="4" width="18" height="16" rx="2" fill="none" stroke="#c99490" stroke-width="1.6"/>
    <line x1="1.5" y1="9" x2="19.5" y2="9" stroke="#c99490" stroke-width="1.6"/>
    <line x1="6" y1="1.5" x2="6" y2="6" stroke="#c99490" stroke-width="1.6"/>
    <line x1="15" y1="1.5" x2="15" y2="6" stroke="#c99490" stroke-width="1.6"/>
    <circle cx="18" cy="18" r="6" fill="#fff" stroke="#c99490" stroke-width="1.6"/>
    <path d="M18 15v3.3l2 1.2" stroke="#c99490" stroke-width="1.4" fill="none"/>
  </svg>
  <div class="abs info" style="left:583px">MON TO FRI: 10.30 AM TO 9.30PM<br>SAT AND HOLIDAY: 10.30 AM TO 7.30PM</div>
</header>

<nav class="abs nav">
  <span class="active-bg"></span>
  <a style="left:101px">HOME</a>
  <a style="left:210px">ABOUT US</a>
  <a style="left:346px">PROMOTIONS</a>
  <a style="left:490px">TREATMENT</a>
  <a style="left:625px">PRODUCTS</a>
  <a style="left:760px">CONTACT US</a>
</nav>

<main>
  <h1 class="abs title" style="top:156px">ABOUT US</h1>
  <svg class="abs divider" style="top:195px" viewBox="0 0 75 14" aria-hidden="true">
    <line x1="0" y1="7" x2="22" y2="7" stroke="#d8b3ae"/>
    <circle cx="37.5" cy="7" r="6" fill="none" stroke="#d8b3ae" stroke-width="1.5"/>
    <line x1="53" y1="7" x2="75" y2="7" stroke="#d8b3ae"/>
  </svg>

  <p class="abs about-copy" style="top:225px">Lumina Beauty has been open for business since May 2011. As our name suggests, we are dedicated to providing your beauty with the best quality in every facet. We have gathered a skilful team of beauty specialist to bring to you the most professionals and current beautifying equipment and products.</p>
  <p class="abs about-copy" style="top:272px">We invite you to relieve yourself of the stress that comes with the Hong Kong lifestyle and enjoy our Lumina Beauty services under a modern and comfortable atmosphere. Our team of well trained specialist will listen to your needs and help you to design a unique treatment plan. We are committed towards improving your youth and it is important to us for each of your visits to be of high quality and relax in manner, services and satisfaction.</p>

  <section class="abs gallery-band"></section>
  <h2 class="abs title" style="top:396px">GALLERY</h2>
  <svg class="abs divider" style="top:436px" viewBox="0 0 75 14" aria-hidden="true">
    <line x1="0" y1="7" x2="22" y2="7" stroke="#d8b3ae"/>
    <circle cx="37.5" cy="7" r="6" fill="none" stroke="#d8b3ae" stroke-width="1.5"/>
    <line x1="53" y1="7" x2="75" y2="7" stroke="#d8b3ae"/>
  </svg>

  <div class="abs photo p1" role="img" aria-label="Treatment room with massage bed and wooden blinds"></div>
  <div class="abs photo p2" role="img" aria-label="Dimly lit twin treatment room with beauty equipment"></div>
  <div class="abs photo p3" role="img" aria-label="Reception area with product display cabinets and armchairs"></div>
  <div class="abs photo p4" role="img" aria-label="Consultation room with desk and product shelves"></div>
  <div class="abs photo p5" role="img" aria-label="Salon entrance corridor with name sign on white wall"></div>
  <div class="abs photo p6" role="img" aria-label="Wooden sauna room with bench and bucket"></div>

  <svg class="abs zoom" width="22" height="22" viewBox="0 0 22 22" aria-hidden="true">
    <circle cx="9" cy="9" r="7" fill="none" stroke="#fff" stroke-width="2"/>
    <line x1="14" y1="14" x2="20" y2="20" stroke="#fff" stroke-width="2.5" stroke-linecap="round"/>
    <line x1="5.5" y1="9" x2="12.5" y2="9" stroke="#fff" stroke-width="2"/>
    <line x1="9" y1="5.5" x2="9" y2="12.5" stroke="#fff" stroke-width="2"/>
  </svg>

  <div class="abs load-more">LOAD MORE</div>
</main>

<footer>
  <div class="abs footer"></div>
  <h3 class="abs foot-head" style="left:64px;top:958px">CONTACT INFO</h3>
  <ul class="abs contact-list">
    <li><span class="ic"><svg width="9" height="11" viewBox="0 0 9 11"><path d="M4.5 0A4 4 0 0 0 .5 4c0 3 4 7 4 7s4-4 4-7a4 4 0 0 0-4-4z" fill="#fff"/><circle cx="4.5" cy="4" r="1.5" fill="#111"/></svg></span><span>12/F., Silver Lotus Tower,<br>21-23 Granville Road, Tsim Sha<br>Tsui, Kowloon, Hong Kong</span></li>
    <li style="margin-top:-2px"><span class="ic"><svg width="10" height="10"><circle cx="5" cy="5" r="3.5" fill="none" stroke="#fff" stroke-width="1.3"/></svg></span><span>2318 5476</span></li>
    <li><span class="ic"><svg width="10" height="10" viewBox="0 0 26 26"><path d="M6 3c2-1 3 0 4 2l1 3c.4 1-.3 2-1 2.6l-1 .8c1 2.5 3 4.6 5.5 5.6l.9-1c.7-.7 1.6-1.2 2.6-.8l3 1.2c1.8.8 2.4 2 1.6 3.7-1.3 2.7-4 3.2-7 1.7C10 20 6 15.5 4.4 11 3.3 7.7 3.8 4.3 6 3z" fill="#fff"/></svg></span><span>6952 1037</span></li>
    <li><span class="ic"><svg width="10" height="8" viewBox="0 0 12 9"><rect width="12" height="9" rx="1" fill="#fff"/><path d="M.5.8 6 5 11.5.8" stroke="#111" fill="none" stroke-width="1.2"/></svg></span><span>hello@luminabeauty.com.hk</span></li>
    <li><span class="ic"><svg width="8" height="8"><rect width="8" height="8" rx="1" fill="#fff"/></svg></span><span>Follow Our Community</span></li>
  </ul>

  <div class="abs foot-brand">
    <span class="brand-dot"></span>
    <span class="brand-name">Lumina Beauty</span>
  </div>
  <p class="abs foot-about">Our professional consultant team provides exceptional knowledge and service, for tailor made treatments, customized to meet your specific needs.</p>

  <h3 class="abs foot-head" style="left:645px;top:958px">LINKS</h3>
  <ul class="abs links">
    <li>Home</li><li>About Us</li><li>Promotion</li><li>Body Treatments</li><li>Facial Treatments</li><li>Slimming Treatments</li><li>Products</li><li>Contact Us</li><li>Join Us</li>
  </ul>

  <div class="abs copyright">Copyright © 2018 Lumina Beauty HK Ltd. All Rights Reserved. Privacy Policy | Terms of Use</div>
</footer>

</body>
</html>
```